Business cards to launch an education platform

Hi,
I am looking at having new business cards designed.
I am a startup, developing a web platform for schools and university, the education world. It's an online assessment system.
I would like a card that looks classy, and that is using the colors and the font of my logo.

I have attached:
1) my logo
2) A business card that I have designed quickly so you can have all the information required in the card, but I really don't like it.
3) The font that I am using (Lato Regular) to design my web platform
4) Some screenshots of my web platform so you can have a look at the style that I have.

Target Market(s)

Major market: Education system: Schools and university
Minor markets: Business in general

Industry/Entity Type

Business

Contact Information for Business Card

Clara Fenwick
Director

M: 0437 518 902
E: clara.fenwick@amberLoomSystems.com.au

Requirements
Must have
• The colors of my logo

```html
<!DOCTYPE html>
<html lang="en">
<head>
<meta charset="utf-8">
<title>Amber Loom Systems — Business Cards</title>
<link rel="stylesheet" href="https://fonts.googleapis.com/css2?family=Lato:wght@300;400;700&display=swap">
<style>
  :root {
    --backdrop: #e9e7e3;
    --card: #ffffff;
    --navy: #0d4a82;
    --blue: #1570b5;
    --cyan: #1fd3ee;
    --ink: #5d6570;
    --ink-soft: #8a929b;
    --edge: rgba(0,0,0,0.14);
  }
  * { box-sizing: border-box; margin: 0; padding: 0; }
  html, body {
    width: 1200px; height: 950px; overflow: hidden;
    background: var(--backdrop);
    font-family: "Lato", Arial, sans-serif;
  }
  .stage { position: relative; width: 1200px; height: 950px; }

  .card {
    position: absolute;
    width: 630px; height: 360px;
    background: var(--card);
    box-shadow: 0 12px 30px var(--edge), 0 2px 4px var(--edge);
    overflow: hidden;
  }
  .card--front { left: 70px; top: 80px; }
  .card--back  { left: 500px; top: 510px; }

  /* front */
  .front-band {
    position: absolute; left: 0; top: 0; width: 100%; height: 92px;
    background: linear-gradient(90deg, var(--cyan) 0%, #3aa6d8 28%, var(--blue) 55%, var(--navy) 100%);
  }
  .holder {
    position: absolute; right: 32px; top: 22px; text-align: right;
  }
  .holder-name { color: var(--cyan); font-size: 24px; font-weight: 400; filter: brightness(1.15); }
  .holder-role { color: #ffffff; font-size: 14px; font-weight: 300; margin-top: 2px; }

  .brand {
    position: absolute; left: 32px; top: 124px;
    display: flex; align-items: center; gap: 14px;
  }
  .brand-square { width: 38px; height: 38px; background: var(--blue); }
  .brand-name {
    color: var(--navy); font-size: 26px; font-weight: 400;
    letter-spacing: 3px; text-transform: uppercase; line-height: 1.05;
  }

  .contacts {
    position: absolute; left: 32px; bottom: 30px;
    list-style: none; color: var(--ink); font-size: 14px; font-weight: 400;
  }
  .contacts li { display: flex; align-items: center; gap: 10px; margin-top: 7px; }
  .contacts svg { width: 14px; height: 14px; flex: none; }

  /* back */
  .back-brand {
    position: absolute; left: 0; right: 0; top: 50%; transform: translateY(-50%);
    display: flex; justify-content: center; align-items: center; gap: 14px;
  }
  .back-brand .brand-square { width: 46px; height: 46px; }
  .back-brand .brand-name { font-size: 30px; }
  .back-web {
    position: absolute; left: 26px; top: 50%;
    transform: translate(-50%, -50%) rotate(-90deg) translateY(0);
    transform-origin: center;
    color: var(--ink); font-size: 14px; white-space: nowrap;
    margin-left: 10px;
  }
</style>
</head>
<body>
<div class="stage">

  <section class="card card--front" aria-label="Business card front">
    <div class="front-band"></div>
    <div class="holder">
      <p class="holder-name">Clara Fenwick</p>
      <p class="holder-role">Director</p>
    </div>

    <div class="brand">
      <span class="brand-square" aria-hidden="true"></span>
      <p class="brand-name">Amber Loom Systems</p>
    </div>

    <ul class="contacts">
      <li>
        <svg viewBox="0 0 14 14" aria-hidden="true"><rect x="3" y="1" width="8" height="12" rx="1.5" fill="none" stroke="#1570b5" stroke-width="1.6"/></svg>
        0437 518 902
      </li>
      <li>
        <svg viewBox="0 0 14 14" aria-hidden="true"><rect x="1" y="3" width="12" height="8" fill="#1570b5"/><path d="M1 3 L7 8 L13 3" fill="none" stroke="#fff" stroke-width="1.2"/></svg>
        clara.fenwick@amberLoomSystems.com.au
      </li>
      <li>
        <svg viewBox="0 0 14 14" aria-hidden="true"><circle cx="7" cy="7" r="6" fill="#1570b5"/><path d="M1 7 H13 M7 1 C4 4 4 10 7 13 M7 1 C10 4 10 10 7 13" fill="none" stroke="#fff" stroke-width="0.9"/></svg>
        www.amberLoomSystems.com.au
      </li>
    </ul>
  </section>

  <section class="card card--back" aria-label="Business card back">
    <div class="back-brand">
      <span class="brand-square" aria-hidden="true"></span>
      <p class="brand-name">Amber Loom Systems</p>
    </div>
    <p class="back-web">www.amberLoomSystems.com.au</p>
  </section>

</div>
</body>
</html>
```